Ferncliff Capital - Website Design

We need a website design for a new commercial real estate company called Ferncliff Capital. We're effectively commercial mortgage brokers connecting real estate investors to lenders. We need a website that is simple (not busy), elegant, professional, and user-friendly. A lot of the users will be in their 50's and less tech savvy, so a stream-lined design is best. The website will serve as a portal for lenders to review new financing opportunities, as well as for real estate investors to review terms from lenders.
Updates
Just uploaded our logo.
Target Market(s)
Commercial real estate investors and lenders
Industry/Entity Type
Real Estate
Number of Pages Required
1 page
Colors
Designer to choose colors to be used in the design.
Look and feel

```html
<!DOCTYPE html>
<html lang="en">
<head>
<meta charset="utf-8">
<title>Ferncliff Capital</title>
<link href="https://fonts.googleapis.com/css2?family=Questrial&family=Open+Sans:ital,wght@0,400;0,600;0,700;1,400&display=swap" rel="stylesheet">
<style>
:root{
  --orange:#f37021;
  --orange-soft:rgba(243,112,33,.86);
  --ink:#2f2f2f;
  --body:#555;
  --muted:#8a8a8a;
  --band:#f3f3f3;
  --circle:#ededed;
  --footer:#3c3c3c;
  --footer-text:#d9d9d9;
  --white:#fff;
}
*{margin:0;padding:0;box-sizing:border-box}
html,body{width:1200px;height:2769px;overflow:hidden;background:var(--white)}
body{font-family:"Open Sans",Arial,sans-serif;color:var(--body)}
.page{position:relative;width:1200px;height:2769px;overflow:hidden}
.abs{position:absolute}
.display{font-family:"Questrial","Century Gothic",sans-serif}

/* header */
.topline{left:0;top:0;width:1200px;height:5px;background:var(--orange)}
.brand{left:161px;top:26px;font-family:"Questrial",sans-serif;font-size:22px;color:var(--ink)}
.nav a{position:absolute;top:32px;transform:translateX(-50%);font-size:12px;color:var(--ink);text-decoration:none;letter-spacing:.3px;white-space:nowrap}
.nav a.active{color:var(--orange)}

/* hero */
.hero{left:0;top:78px;width:1200px;height:502px;background:linear-gradient(100deg,#cfc8bd 0%,#b7ada0 30%,#8d8a86 55%,#5f6670 75%,#3e4650 100%)}
.hero-shade{left:0;top:78px;width:1200px;height:502px;background:rgba(0,0,0,.18)}
.hero-title{left:0;width:1200px;top:236px;text-align:center;color:var(--white);font-size:52px;line-height:61px}
.btn-solid{background:var(--orange);color:var(--white);border-radius:20px;text-align:center;font-weight:700;text-decoration:none}
.hero-btn{left:482px;top:377px;width:236px;height:34px;line-height:34px;font-size:12px}

/* services */
.service{width:230px;transform:translateX(-50%);text-align:center}
.service .ring{width:124px;height:124px;border-radius:50%;background:var(--circle);margin:0 auto;display:flex;align-items:center;justify-content:center}
.service h3{margin-top:33px;font-size:13px;font-weight:600;color:var(--ink)}
.service p{margin-top:20px;font-size:11px;line-height:18px;color:var(--body)}

/* about */
.about{left:0;top:914px;width:1200px;height:360px;background:var(--band)}
.about-title{left:161px;top:964px;font-size:30px;color:var(--ink)}
.about-text{left:161px;top:1010px;width:420px;font-size:10.5px;line-height:19px}
.btn-about{left:161px;top:1172px;width:105px;height:35px;line-height:35px;font-size:12px;font-weight:600}
.video{left:633px;top:973px;width:403px;height:234px;background:linear-gradient(120deg,#6b6460,#a49b93 45%,#d8d3cf 70%,#7d8aa0)}

/* projects */
.section-title{left:0;width:1200px;text-align:center;font-size:28px;color:var(--ink)}
.card{top:1366px;width:203px}
.card .photo{width:203px;height:168px}
.card h4{margin-top:22px;font-family:"Questrial",sans-serif;font-weight:400;font-size:15px;color:var(--ink)}
.card p{margin-top:8px;font-size:10px;line-height:18px}
.btn-outline{display:block;margin-top:14px;width:100px;height:33px;line-height:31px;border:1.5px solid var(--orange);border-radius:17px;color:var(--orange);text-align:center;font-size:11px;text-decoration:none}

/* investors band */
.investors{left:0;top:1741px;width:1200px;height:395px;background:linear-gradient(90deg,#d9c9bb 0%,#efe6de 30%,#f7f3ef 50%,#e6d6c6 70%,#b89c82 100%)}
.invest-box{left:354px;top:1820px;width:491px;height:236px;background:var(--orange-soft);text-align:center;color:var(--white)}
.invest-box h2{margin-top:40px;font-family:"Questrial",sans-serif;font-weight:400;font-size:25px}
.invest-box p{margin:14px auto 0;width:360px;font-size:13px;line-height:26px}
.btn-dark{display:block;margin:14px auto 0;width:104px;height:33px;line-height:33px;border-radius:17px;background:#333;color:var(--white);font-size:12px;text-decoration:none}

/* testimonials */
.quote{left:300px;top:2240px;width:600px;text-align:center;font-style:italic;font-size:11px;line-height:25px;color:var(--body)}
.quote-name{left:0;width:1200px;top:2330px;text-align:center;font-size:11.5px;font-weight:700;color:var(--ink)}
.partner{background:#dcdcdc;top:2400px;height:18px;border-radius:3px}

/* footer */
.footer{left:0;top:2459px;width:1200px;height:247px;background:var(--footer)}
.fcol h5{font-weight:400;font-size:12px;color:var(--white);letter-spacing:.4px;margin-bottom:18px}
.fcol a{display:block;font-size:11px;line-height:26px;color:var(--footer-text);text-decoration:none}
.social{display:flex;gap:7px;margin-bottom:22px}
.social span{width:26px;height:26px;border:1.5px solid var(--white);border-radius:50%}
.bottom-bar{left:0;top:2706px;width:1200px;height:63px;background:var(--orange);text-align:center;color:var(--white);font-size:11px;line-height:63px}
</style>
</head>
<body>
<div class="page">

  <div class="abs topline"></div>
  <div class="abs brand">Ferncliff Capital</div>
  <nav class="nav">
    <a class="active" href="#" style="left:447px">HOME</a>
    <a href="#" style="left:521px">WHY US?</a>
    <a href="#" style="left:600px">FINANCE</a>
    <a href="#" style="left:674px">SALES</a>
    <a href="#" style="left:746px">RENTALS</a>
    <a href="#" style="left:844px">DEVELOPMENTS</a>
    <a href="#" style="left:932px">BLOG</a>
    <a href="#" style="left:1006px">CONTACT</a>
  </nav>

  <div class="abs hero" role="img" aria-label="Photo of a smiling couple shaking hands with an agent in a bright modern kitchen"></div>
  <div class="abs hero-shade"></div>
  <h1 class="abs hero-title display">The Best Way to Find<br>Your Perfect Home</h1>
  <a class="abs btn-solid hero-btn" href="#">FIND MORTGAGE BROKER</a>
  <svg class="abs" style="left:32px;top:294px" width="36" height="72" viewBox="0 0 36 72"><polyline points="34,2 2,36 34,70" fill="none" stroke="#fff" stroke-width="2"/></svg>
  <svg class="abs" style="left:1132px;top:294px" width="36" height="72" viewBox="0 0 36 72"><polyline points="2,2 34,36 2,70" fill="none" stroke="#fff" stroke-width="2"/></svg>

  <div class="abs service" style="left:257px;top:628px">
    <div class="ring"><svg width="60" height="64" viewBox="0 0 60 64"><circle cx="30" cy="18" r="14" fill="#6ab04c"/><path d="M4 64 Q4 36 30 36 Q56 36 56 64Z" fill="#6ab04c"/></svg></div>
    <h3>Investors</h3>
    <p>Sed ut perspiciatis unde onis<br>sit voluptatem accusantium dolorue<br>laudantiutem accusantm.</p>
  </div>
  <div class="abs service" style="left:484px;top:628px">
    <div class="ring"><svg width="70" height="60" viewBox="0 0 70 60"><path d="M14 28 L35 8 L56 28 L56 40 L14 40Z" fill="none" stroke="#f5a623" stroke-width="4"/><rect x="31" y="24" width="8" height="8" fill="#f5a623"/><path d="M4 44 Q20 40 30 48 L50 48 Q60 46 66 40 L66 52 L4 56Z" fill="#f5a623"/></svg></div>
    <h3>Home Loans</h3>
    <p>Sed ut perspiciatis unde onis<br>sit voluptatem accusantium dolorue<br>laudantiutem accusantm oti.</p>
  </div>
  <div class="abs service" style="left:716px;top:628px">
    <div class="ring"><svg width="70" height="64" viewBox="0 0 70 64"><path d="M4 36 L22 20 L40 36 L40 60 L4 60Z" fill="#4a5fc1"/><circle cx="52" cy="12" r="8" fill="#4a5fc1"/><rect x="44" y="22" width="16" height="38" rx="4" fill="#4a5fc1"/></svg></div>
    <h3>Mortgage Brokers</h3>
    <p>Sed ut perspiciatis unde onis<br>sit voluptatem accusantium dolorue<br>laudantiutem accusantm oti.</p>
  </div>
  <div class="abs service" style="left:949px;top:628px">
    <div class="ring"><svg width="48" height="62" viewBox="0 0 48 62"><rect x="2" y="2" width="44" height="58" rx="5" fill="none" stroke="#f37021" stroke-width="4"/><rect x="9" y="9" width="30" height="12" fill="#f37021"/><g fill="#f37021"><rect x="9" y="27" width="8" height="7"/><rect x="20" y="27" width="8" height="7"/><rect x="31" y="27" width="8" height="7"/><rect x="9" y="38" width="8" height="7"/><rect x="20" y="38" width="8" height="7"/><rect x="31" y="38" width="8" height="7"/><rect x="9" y="49" width="8" height="6"/><rect x="20" y="49" width="8" height="6"/><rect x="31" y="49" width="8" height="6"/></g></svg></div>
    <h3>Calculators &amp; Tools</h3>
    <p>Sed ut perspiciatis unde onis<br>sit voluptatem accusantium dolorue<br>laudantiutem accusantm oti.</p>
  </div>

  <div class="abs about"></div>
  <h2 class="abs about-title display">Ferncliff Capital</h2>
  <p class="abs about-text">Sed ut perspiciatis unde omnis iste natus error sit voluptatem accusantium doloremque laudantium, totam rem aperiam, eaque ipsa quae ab illo inventore veritatis quasi architecto beatae vitae dicta sunt explicabo. Nemo enim ipsam voluptatemul voluptas sit aspernatur aut odit aut fugit, sed quia consequuntur magni dolores eos qui ratione voluptatem sequi nesciunt. Neque porro quisquam est, qui dolorem ipsum quia dolor sit amet, consectetur, adipisci velit, sed quia non numquam eius modi tempora incidunt ut labore et dolore maui ratione voluptatem sequ.</p>
  <a class="abs btn-solid btn-about" href="#">Read More</a>
  <div class="abs video" role="img" aria-label="Video still of advisors reviewing documents with clients at a meeting table"></div>
  <svg class="abs" style="left:800px;top:1056px" width="68" height="68" viewBox="0 0 68 68"><circle cx="34" cy="34" r="31" fill="none" stroke="#fff" stroke-width="4"/><path d="M26 20 L50 34 L26 48Z" fill="#fff"/></svg>

  <h2 class="abs section-title display" style="top:1310px">Our Recent Projects</h2>
  <svg class="abs" style="left:120px;top:1436px" width="16" height="30" viewBox="0 0 16 30"><polyline points="14,1 2,15 14,29" fill="none" stroke="#999" stroke-width="1.5"/></svg>
  <svg class="abs" style="left:1065px;top:1436px" width="16" height="30" viewBox="0 0 16 30"><polyline points="2,1 14,15 2,29" fill="none" stroke="#999" stroke-width="1.5"/></svg>

  <div class="abs card" style="left:161px">
    <div class="photo" role="img" aria-label="Photo of a hand signing papers beside a small model house" style="background:linear-gradient(135deg,#e9e3da,#c9a37a 60%,#8a5a36)"></div>
    <h4>Finibus Bonorumeta</h4>
    <p>At vero eos et accusa lomust iusto dissimos ducimus qui blanditiispaeloe ntium voluptatut vers et accu.</p>
    <a class="btn-outline" href="#">Read More</a>
  </div>
  <div class="abs card" style="left:386px">
    <div class="photo" role="img" aria-label="Photo of a couple looking at a house under a blue sky" style="background:linear-gradient(180deg,#4f8fd6,#9cc3e8 45%,#3a5f8f)"></div>
    <h4>Finibus Bonorumeta</h4>
    <p>At vero eos et accusa lomust iusto dissimos ducimus qui blanditiispaeloe ntium voluptatut vers et accu.</p>
    <a class="btn-outline" href="#">Read More</a>
  </div>
  <div class="abs card" style="left:611px">
    <div class="photo" role="img" aria-label="Photo of an agent showing a tablet to a couple by the sea" style="background:linear-gradient(135deg,#a9c7dc,#5a6a7a 55%,#2f3640)"></div>
    <h4>Finibus Bonorumeta</h4>
    <p>At vero eos et accusa lomust iusto dissimos ducimus qui blanditiispaeloe ntium voluptatut vers et accu.</p>
    <a class="btn-outline" href="#">Read More</a>
  </div>
  <div class="abs card" style="left:836px">
    <div class="photo" role="img" aria-label="Photo of a modern white villa with a pool at dusk" style="background:linear-gradient(180deg,#1f5fc7,#6e9be0 50%,#e8e8ea 70%,#3a7fd0)"></div>
    <h4>Finibus Bonorumeta</h4>
    <p>At vero eos et accusa lomust iusto dissimos ducimus qui blanditiispaeloe ntium voluptatut vers et accu.</p>
    <a class="btn-outline" href="#">Read More</a>
  </div>

  <div class="abs investors" role="img" aria-label="Photo of a smiling woman and couple discussing plans"></div>
  <div class="abs invest-box">
    <h2>Real Estate Investors</h2>
    <p>Lorem ipsum dolor sit amet, consectetur adipis sed do eiusmod tempor incididunt ut labore dolore magna aliqua. Ut enim ad minim veniamore.</p>
    <a class="btn-dark" href="#">Read More</a>
  </div>

  <h2 class="abs section-title display" style="top:2176px">Client Testimonials</h2>
  <svg class="abs" style="left:222px;top:2264px" width="38" height="16" viewBox="0 0 38 16"><path d="M37 8 H2 M9 1 L2 8 L9 15" fill="none" stroke="#999" stroke-width="1.5"/></svg>
  <svg class="abs" style="left:940px;top:2264px" width="38" height="16" viewBox="0 0 38 16"><path d="M1 8 H36 M29 1 L36 8 L29 15" fill="none" stroke="#999" stroke-width="1.5"/></svg>
  <p class="abs quote">Lorem ipsum dolor sit amet, consectetur adipiscing elit, sed do eiusmod tempor incididunt ut labore dolore magna aliqua. Ut enim ad minim veniam,Lorem ipsum dolor sit amet, consectetur adipiscing elied do eiusmod tempor incididunt ut labore et dolore magna aliqua. Ut enim ad minim veniam,</p>
  <p class="abs quote-name">DANA WHITMORE, <span style="font-weight:600">CITY NAME</span></p>
  <div class="abs partner" style="left:300px;width:120px"></div>
  <div class="abs" style="left:469px;top:2395px;width:30px;height:30px;border-radius:50%;background:#dcdcdc"></div>
  <div class="abs partner" style="left:545px;width:70px"></div>
  <div class="abs partner" style="left:654px;width:110px"></div>
  <div class="abs partner" style="left:801px;width:98px"></div>

  <div class="abs footer"></div>
  <div class="abs fcol" style="left:161px;top:2496px"><h5>ABOUT</h5><a>About</a><a>Financial</a><a>Projects</a><a>Team</a><a>News</a></div>
  <div class="abs fcol" style="left:297px;top:2496px"><h5>INFORMATION</h5><a>Real Estate Investors</a><a>Mortgage brokers</a><a>Sed uerspiciatis</a><a>Comnisteatusit</a><a>Perspiciatis unde</a></div>
  <div class="abs fcol" style="left:513px;top:2496px"><h5>WHO WE ARE</h5><a>Sed uterspiciatis</a><a>Find Brokers</a><a>Perspiciatis unde</a><a>Sed uerspiciatem</a><a>Comnisteatusit</a></div>
  <div class="abs fcol" style="left:709px;top:2496px"><h5>CONNECT</h5>
    <div class="social"><span></span><span></span><span></span><span></span><span></span></div>
    <h5 style="margin-bottom:8px">POLICIES</h5><a>Privacy</a><a>Complaint and Feedback</a></div>
  <div class="abs fcol" style="left:927px;top:2496px"><h5>OTHER LINKS</h5><a>Sed uterspiciatis</a><a>Perspici loreati</a><a>Perspiciatis unde</a><a>Sed uerspiciatem</a><a>Comnisteatusit</a></div>

  <div class="abs bottom-bar">© 2017 &nbsp;Ferncliff Capital. Privacy Policy &nbsp;|&nbsp; Terms of Use &nbsp;|&nbsp; Contact</div>
</div>
</body>
</html>
```